Mosquito and outdoor pest management

The uploaded logo must be integrated as the main theme of the card. I would like it to be modern and eye catching. Maybe some backround images or light silver metallic background.
Space enough at the base for contact info to be put in- phone numbers,emails,names,website.
Space on the back for short blog and lines for hand writing..calling card.
Commercial- golf courses, schools, outdoor function properties, pre event treatments.
Residential- retirement villages, townhome complexes and general houses
Management

```html
<!DOCTYPE html>
<html lang="en">
<head>
<meta charset="utf-8">
<title>Coastline Mosquito – Business Card</title>
<link rel="stylesheet" href="https://fonts.googleapis.com/css2?family=Open+Sans:wght@400;600&family=Crimson+Text:wght@400&display=swap">
<style>
  :root {
    --red: #e8222e;
    --black: #111111;
    --ink: #2b2b2b;
    --grey: #555555;
    --paper: #ffffff;
    --silver: #e9e9e9;
    --backdrop: #d9d6d0;
  }
  * { box-sizing: border-box; margin: 0; padding: 0; }
  html, body { width: 1200px; height: 892px; overflow: hidden; }
  body {
    background: var(--backdrop);
    font-family: "Open Sans", Arial, sans-serif;
    color: var(--ink);
    position: relative;
  }
  .card {
    position: absolute;
    left: 290px;
    width: 620px;
    height: 350px;
    overflow: hidden;
    box-shadow: 0 6px 18px rgba(0,0,0,.25);
  }
  .card--front { top: 58px; background: var(--paper); }
  .card--back { top: 470px; background: linear-gradient(160deg, var(--paper) 0%, var(--silver) 100%); }

  /* front */
  .edge-band { position: absolute; right: 0; top: 0; width: 110px; height: 350px; }
  .brand {
    position: absolute; left: 38px; top: 70px;
    display: flex; align-items: center; gap: 12px;
  }
  .brand__mark { width: 16px; height: 16px; background: var(--red); }
  .brand__name { font-size: 21px; font-weight: 600; color: var(--ink); letter-spacing: .5px; }
  .person { position: absolute; left: 330px; top: 150px; width: 180px; text-align: right; }
  .person__name { font-size: 24px; font-weight: 600; color: var(--red); line-height: 1.1; }
  .person__role { font-size: 14px; color: var(--ink); margin-top: 6px; }
  .rule-name { position: absolute; left: 38px; top: 182px; width: 300px; height: 1.5px; background: var(--ink); }
  .contacts { position: absolute; left: 38px; top: 232px; list-style: none; }
  .contacts li { display: flex; align-items: center; gap: 12px; font-size: 15px; color: var(--ink); height: 26px; }
  .contacts svg { width: 16px; height: 16px; flex: none; }

  /* back */
  .back-tab { position: absolute; left: 0; top: 0; width: 46px; height: 350px; }
  .services__rule { position: absolute; left: 86px; top: 30px; width: 440px; height: 1px; background: var(--red); }
  .services { position: absolute; left: 86px; top: 42px; }
  .services__heading { font-family: "Crimson Text", Georgia, serif; font-size: 23px; font-weight: 400; color: var(--ink); line-height: 1.2; }
  .services__list { list-style: none; margin: 6px 0 12px 18px; }
  .services__list li { font-size: 14.5px; line-height: 22px; color: var(--ink); position: relative; padding-left: 18px; }
  .services__list li::before {
    content: ""; position: absolute; left: 0; top: 8px; width: 7px; height: 7px;
    background: var(--red); border-radius: 50%;
  }
  .services__list--plain li { padding-left: 0; }
  .services__list--plain li::before { display: none; }
</style>
</head>
<body>

<section class="card card--front" aria-label="Card front">
  <svg class="edge-band" viewBox="0 0 110 350" aria-hidden="true">
    <polygon points="30,0 110,0 110,350 30,350" fill="var(--red)"/>
    <polygon points="30,232 52,212 110,212 110,350 30,350" fill="var(--black)"/>
    <polygon points="38,236 56,220 110,220 110,224 58,224 42,238" fill="#ffffff" opacity=".35"/>
  </svg>

  <div class="brand">
    <span class="brand__mark"></span>
    <span class="brand__name">Coastline Mosquito &amp; Outdoor Pest Care</span>
  </div>

  <div class="rule-name"></div>
  <div class="person">
    <div class="person__name">Liam Hartley</div>
    <div class="person__role">Director</div>
  </div>

  <ul class="contacts">
    <li>
      <svg viewBox="0 0 16 16" aria-hidden="true"><rect width="16" height="16" fill="var(--red)"/><rect x="5" y="3" width="6" height="10" rx="1" fill="none" stroke="#fff" stroke-width="1.2"/></svg>
      0400 123 456
    </li>
    <li>
      <svg viewBox="0 0 16 16" aria-hidden="true"><rect width="16" height="16" fill="var(--red)"/><path d="M4 4c0 5 3 8 8 8l1-2-2-1-1 1c-2-1-3-2-4-4l1-1-1-2z" fill="#fff"/></svg>
      (07) 5550 1234
    </li>
    <li>
      <svg viewBox="0 0 16 16" aria-hidden="true"><rect width="16" height="16" fill="var(--red)"/><rect x="3" y="5" width="10" height="7" fill="none" stroke="#fff" stroke-width="1.2"/><path d="M3 5l5 4 5-4" fill="none" stroke="#fff" stroke-width="1.2"/></svg>
      hello@coastmozzie.com
    </li>
    <li>
      <svg viewBox="0 0 16 16" aria-hidden="true"><rect width="16" height="16" fill="var(--red)"/><circle cx="8" cy="8" r="4.5" fill="none" stroke="#fff" stroke-width="1.2"/><path d="M3.5 8h9M8 3.5c-2 3-2 6 0 9M8 3.5c2 3 2 6 0 9" fill="none" stroke="#fff" stroke-width="1"/></svg>
      www.coastmozzie.com
    </li>
  </ul>
</section>

<section class="card card--back" aria-label="Card back">
  <svg class="back-tab" viewBox="0 0 46 350" aria-hidden="true">
    <rect x="0" y="0" width="46" height="350" fill="var(--black)"/>
    <polygon points="0,0 30,0 30,150 18,165 0,165" fill="var(--red)"/>
  </svg>

  <div class="services__rule"></div>
  <div class="services">
    <h2 class="services__heading">Commercial</h2>
    <ul class="services__list">
      <li>golf courses,</li>
      <li>schools,</li>
      <li>outdoor function properties,</li>
      <li>pre event treatments.</li>
    </ul>
    <h2 class="services__heading">Residential</h2>
    <ul class="services__list services__list--plain">
      <li>retirement villages,</li>
      <li>townhome complexes and general houses.</li>
    </ul>
  </div>
</section>

</body>
</html>
```